Laser Tattoo Removal Business Cards

We are looking for a professional business card design for a laser tattoo removal business. Ideally looking for a black business card design. The name of the business is Brightline Tattoo Removal. We place our cards at local tattoo shops so we ideally are looking for something trendy/edgy to draw both male and female clientele in.

Target Market(s)

Male/Female ages 18-60

Contact Information for Business Card

black background ideally.. hoping to stay within greys, whites and black

Font styles to use
Serif
Sans Serif

Colors
121212
a9a9a9
5c5c5c
f5f5f5
ffffff
7f7f7f
606060
848484
9d9d9d

Requirements
Must have
• Employee Info:
• Melissa Thornbury
• Chief Executive Offer
• m: 919.537.2846
• w: 919.362.4178
• f: 919.685.3907
• mthornbury@brightlinetattooremoval.example
• Address:
• 4615 Oakmere Pkwy, Suite 210
• Raleigh, NC 27654
• Website:
• www.brightlinetattooremoval.example
Nice to have
• Myabe business name on back or logo on back and employee info on the front

```html
<!DOCTYPE html>
<html lang="en">
<head>
<meta charset="utf-8">
<title>Brightline Tattoo Removal – Business Cards</title>
<link rel="stylesheet" href="https://fonts.googleapis.com/css2?family=Questrial&display=swap">
<style>
  :root {
    --backdrop: #2b2724;
    --card-black: #121212;
    --card-white: #f5f5f5;
    --ink-white: #ffffff;
    --ink-dark: #121212;
    --grey-light: #a9a9a9;
    --grey-mid: #7f7f7f;
    --grey-deep: #5c5c5c;
    --band: #1c1c1c;
  }
  * { box-sizing: border-box; margin: 0; padding: 0; }
  html, body {
    width: 1200px; height: 715px; overflow: hidden;
    background: var(--backdrop);
    font-family: "Questrial", "Century Gothic", sans-serif;
  }
  .stage {
    position: relative; width: 1200px; height: 715px;
    display: flex; align-items: center; justify-content: center; gap: 60px;
  }
  .card {
    position: relative; width: 520px; height: 297px;
    box-shadow: 0 14px 30px rgba(0,0,0,.45);
    overflow: hidden;
  }
  .card--front { background: var(--card-black); color: var(--ink-white); }
  .card--back { background: var(--card-white); color: var(--ink-dark); }

  .brand {
    position: absolute; left: 0; right: 0; top: 62px;
    text-align: center;
  }
  .card--back .brand { top: 34px; }
  .brand__name {
    font-size: 44px; letter-spacing: 5px; line-height: 1;
  }
  .brand__sub {
    margin-top: 12px; font-size: 15px; letter-spacing: 4px;
  }
  .card--front .brand__name,
  .card--front .brand__sub { color: var(--grey-light); }

  .website {
    position: absolute; left: 0; right: 0; bottom: 52px;
    text-align: center; font-size: 14px; letter-spacing: 1.5px;
    color: var(--ink-white);
  }

  .employee {
    position: absolute; right: 300px; top: 140px; text-align: right;
  }
  .employee__name { font-size: 14px; color: var(--ink-dark); }
  .employee__title { font-size: 12px; color: var(--grey-deep); margin-top: 3px; }

  .divider {
    position: absolute; left: 232px; top: 138px; width: 1px; height: 100px;
    background: linear-gradient(var(--grey-light), var(--ink-dark), var(--grey-light));
  }

  .contact {
    position: absolute; left: 248px; top: 140px; list-style: none;
    font-size: 12px; color: var(--ink-dark);
  }
  .contact li { display: flex; align-items: center; gap: 9px; height: 19px; }
  .contact svg { width: 11px; height: 11px; fill: var(--ink-dark); flex: none; }

  .address-band {
    position: absolute; left: 0; right: 0; bottom: 0; height: 46px;
    background: var(--band); color: var(--ink-white);
    display: flex; align-items: center; justify-content: center;
    font-size: 12.5px; letter-spacing: .4px;
  }
</style>
</head>
<body>
<main class="stage">

  <section class="card card--front" aria-label="Card front">
    <div class="brand">
      <div class="brand__name">BRIGHTLINE</div>
      <div class="brand__sub">TATTOO REMOVAL</div>
    </div>
    <p class="website">www.brightlinetattooremoval.example</p>
  </section>

  <section class="card card--back" aria-label="Card back">
    <div class="brand">
      <div class="brand__name">BRIGHTLINE</div>
      <div class="brand__sub">TATTOO REMOVAL</div>
    </div>

    <div class="employee">
      <p class="employee__name">Melissa Thornbury</p>
      <p class="employee__title">Chief Executive Offer</p>
    </div>

    <span class="divider"></span>

    <ul class="contact">
      <li>
        <svg viewBox="0 0 12 12" aria-hidden="true"><path d="M1 3.5C1 2.5 2.5 2 6 2s5 .5 5 1.5V5H8.5V4h-5v1H1zM2.5 6h7l.8 4.5H1.7zM6 7a1.2 1.2 0 1 0 0 2.4A1.2 1.2 0 0 0 6 7z"/></svg>
        919.537.2846
      </li>
      <li>
        <svg viewBox="0 0 12 12" aria-hidden="true"><path d="M2.5 1.2l2 .2.9 2.5-1.2 1a6 6 0 0 0 2.9 2.9l1-1.2 2.5.9.2 2c-.3.6-1 .9-1.6.9A8 8 0 0 1 1.5 2.8c0-.6.4-1.3 1-1.6z"/></svg>
        919.362.4178
      </li>
      <li>
        <svg viewBox="0 0 12 12" aria-hidden="true"><path d="M3 1h6v3H3zM1 4.5h10v5H9V8H3v1.5H1zM3.5 8.5h5V11h-5z"/></svg>
        919.685.3907
      </li>
      <li>
        <svg viewBox="0 0 12 12" aria-hidden="true"><path d="M1 2.5h10v7H1zm1 1v.4l4 2.6 4-2.6v-.4zm0 1.6v3.4h8V5.1L6 7.7z"/></svg>
        mthornbury@brightlinetattooremoval.example
      </li>
    </ul>

    <footer class="address-band">4615 Oakmere Pkwy, Suite 210, Raleigh, NC 27654</footer>
  </section>

</main>
</body>
</html>
```